Business Card Design

Hi I need a business card designed, we already have the business name logo artwork and would like some concept ideas for the Bus Card layout.
On the back of the card i want to include the products and services that we offer.
We are a Plastics Sheeting manufacture based in Perth Australia.

                                       

We need a BC design for a company called Tarvo Plastics based in Perth Australia.

We supply from DIY to Trade & Industrial  Engineering Markets.

We specialise in:

·         Cut to size panels  (all shapes and sizes)

·         Plastics fabrication & Welding

·         Custom Designs

·         Plastic Repairs

·         PVC Pipe Slotting & PVC Pipe Threading

·         Supplier of all types of engineering plastics and profiles.

Including:           Acrylic / Clarvene

                               Polycarbonate / Dorvil

                               Prismatic Light Diffuser

                               Vantrib

                               HDPE / UHMWPE

                               PVC / PVC Foam

                               Nylon

                               HIPS

```html
<!DOCTYPE html>
<html lang="en">
<head>
<meta charset="utf-8">
<title>Tarvo Plastics – Business Card</title>
<link href="https://fonts.googleapis.com/css2?family=Open+Sans:wght@400;600;700&display=swap" rel="stylesheet">
<style>
  :root {
    --navy: #1d2a6b;
    --orange: #e8862a;
    --blue: #2f8cc9;
    --grey: #5a5a5a;
    --white: #ffffff;
    --backdrop: #eceae6;
  }
  * { box-sizing: border-box; margin: 0; padding: 0; }
  html, body {
    width: 1200px; height: 720px; overflow: hidden;
    background: var(--backdrop);
    font-family: "Open Sans", Arial, sans-serif;
  }
  .stage {
    position: relative; width: 1200px; height: 720px;
    display: flex; align-items: center; justify-content: center; gap: 40px;
  }
  .card {
    position: relative; width: 540px; height: 310px;
    box-shadow: 0 6px 18px rgba(0,0,0,.18);
    overflow: hidden;
  }

  /* Front */
  .card-front { background: var(--white); color: var(--grey); }
  .brand-name {
    font-weight: 700; letter-spacing: .5px;
    display: flex; align-items: center; gap: 10px;
    white-space: nowrap;
  }
  .brand-mark { width: 18px; height: 18px; display: inline-block; flex: none; }
  .card-front .brand-name {
    position: absolute; top: 40px; left: 92px;
    font-size: 46px; color: var(--navy);
  }
  .card-front .brand-mark { background: var(--orange); }
  .identity {
    position: absolute; top: 148px; left: 40px; width: 220px;
    text-align: right;
  }
  .person-name { color: var(--navy); font-weight: 700; font-size: 17px; line-height: 1.2; }
  .person-title { color: var(--orange); font-weight: 600; font-size: 12px; margin-bottom: 6px; }
  .address { font-size: 12.5px; line-height: 1.35; margin-top: 4px; }
  .divider-front {
    position: absolute; top: 140px; left: 278px; width: 1px; height: 135px;
    background: #c9c9c9;
  }
  .contacts {
    position: absolute; top: 140px; left: 296px; list-style: none;
    font-size: 12.5px; line-height: 1.65;
  }
  .contacts li { display: flex; align-items: center; gap: 8px; white-space: nowrap; }
  .contacts svg { width: 13px; height: 13px; flex: none; }
  .contacts .company-line { display: block; margin-top: 6px; font-size: 12px; line-height: 1.35; }

  /* Back */
  .card-back { background: var(--blue); color: var(--white); }
  .card-back .brand-name {
    position: absolute; top: 22px; left: 0; right: 0; justify-content: center;
    font-size: 40px;
  }
  .card-back .brand-mark { background: var(--white); }
  .tagline {
    position: absolute; top: 86px; left: 0; right: 0; text-align: center;
    font-weight: 700; font-size: 13.5px; line-height: 1.35;
  }
  .offer { position: absolute; top: 134px; }
  .offer h2 { font-size: 16px; font-weight: 700; margin-bottom: 4px; }
  .offer ul { list-style: none; font-size: 12.5px; line-height: 1.45; }
  .offer li::before { content: "• "; }
  .services { left: 30px; width: 300px; }
  .materials { left: 352px; width: 180px; }
  .materials li { white-space: nowrap; }
  .divider-back {
    position: absolute; top: 140px; left: 338px; width: 1px; height: 140px;
    background: rgba(255,255,255,.6);
  }
</style>
</head>
<body>
<main class="stage">

  <section class="card card-front" aria-label="Business card front">
    <div class="brand-name"><span class="brand-mark"></span>Tarvo Plastics</div>

    <div class="identity">
      <p class="person-name">Your Name</p>
      <p class="person-title">Title</p>
      <p class="address">Unit 4/18 Marlow Circuit<br>Brookdale WA 6412</p>
      <p class="address">PO Box 2284<br>Brookdale DC WA 6418</p>
    </div>

    <div class="divider-front"></div>

    <ul class="contacts">
      <li>
        <svg viewBox="0 0 16 16"><circle cx="8" cy="8" r="8" fill="var(--orange)"/><path d="M5 4h2l1 2.5-1.2.8a5 5 0 0 0 2 2l.8-1.2L12 9v2a1 1 0 0 1-1 1A7 7 0 0 1 4 5a1 1 0 0 1 1-1z" fill="#fff"/></svg>
        08 9300 4100
      </li>
      <li>
        <svg viewBox="0 0 16 16"><circle cx="8" cy="8" r="8" fill="var(--orange)"/><rect x="5.5" y="3.5" width="5" height="9" rx="1" fill="#fff"/><rect x="6.5" y="4.8" width="3" height="5" fill="var(--orange)"/></svg>
        123-555-0148
      </li>
      <li>
        <svg viewBox="0 0 16 16"><circle cx="8" cy="8" r="8" fill="var(--orange)"/><rect x="4" y="7" width="8" height="5" rx="1" fill="#fff"/><rect x="5.5" y="4" width="5" height="3.5" fill="#fff"/></svg>
        08 9300 4122
      </li>
      <li>
        <svg viewBox="0 0 16 16"><circle cx="8" cy="8" r="8" fill="var(--orange)"/><rect x="3.5" y="5" width="9" height="6.5" rx=".8" fill="#fff"/><path d="M3.8 5.4 8 8.6l4.2-3.2" stroke="var(--orange)" stroke-width="1" fill="none"/></svg>
        sales@tarvoplastics.com.au
      </li>
      <li class="company-line">Kessel Holdings Pty Ltd<br>T/A Tarvo Plastics ABN: TBA</li>
    </ul>
  </section>

  <section class="card card-back" aria-label="Business card back">
    <div class="brand-name"><span class="brand-mark"></span>Tarvo Plastics</div>

    <p class="tagline">The Products And Services That We Offer<br>Are Supplied From Diy To Trade &amp; Industrial Engineering Markets</p>

    <div class="offer services">
      <h2>We specialise in:</h2>
      <ul>
        <li>Cut to size panels (all shapes and sizes)</li>
        <li>Plastics fabrication &amp; Welding</li>
        <li>Custom Designs</li>
        <li>Plastic Repairs</li>
        <li>PVC Pipe Slotting &amp; PVC Pipe Threading</li>
        <li>Supplier of all types of engineering plastics and profiles</li>
      </ul>
    </div>

    <div class="divider-back"></div>

    <div class="offer materials">
      <h2>Including:</h2>
      <ul>
        <li>Acrylic / Clarvene</li>
        <li>Polycarbonate / Dorvil</li>
        <li>Prismatic Light Diffuser</li>
        <li>Vantrib &nbsp;• HDPE / UHMWPE</li>
        <li>PVC / PVC Foam</li>
        <li>Nylon &nbsp;• HIPS</li>
      </ul>
    </div>
  </section>

</main>
</body>
</html>
```